New Business Card Design Project

Use the flyer uploaded and website www.brightoakbuilders.com for inspiration.
List Our Services on Backside of business cards
Marcus Delling
Harborline Builders Inc.
Licensed General Contractors
858-471-6093

Contact Information for Business Card

Use the flyer uploaded and website www.brightoakbuilders.com for inspiration. List Our Services on Backside of business cards Marcus Delling Harborline Builders Inc. Licensed General Contractors 858-471-6093

```html
<!DOCTYPE html>
<html lang="en">
<head>
<meta charset="utf-8">
<title>Harborline Builders – Business Card</title>
<link rel="stylesheet" href="https://fonts.googleapis.com/css2?family=Marcellus&family=Arimo:wght@400&display=swap">
<style>
  :root {
    --page: #e4e4e4;
    --card: #333333;
    --card-soft: #3b3b3b;
    --ink: #ffffff;
    --rule: #d9d9d9;
    --band-light: #efeff1;
    --band-grey: #aaa7a8;
    --band-text: #333333;
  }
  * { box-sizing: border-box; margin: 0; padding: 0; }
  html, body { width: 1200px; height: 1040px; overflow: hidden; }
  body { background: var(--page); position: relative; font-family: "Arimo", Arial, sans-serif; color: var(--ink); }

  .card {
    position: absolute; left: 200px; width: 800px; height: 458px;
    background: var(--card); border-radius: 22px; overflow: hidden;
  }
  .card--front { top: 30px; }
  .card--back { top: 556px; }

  .brand-name {
    position: absolute; left: 420px; width: 360px; top: 160px; text-align: center;
    font-family: "Marcellus", serif; font-size: 25px; letter-spacing: 1.5px; color: var(--ink);
  }
  .person-name {
    position: absolute; left: 52px; top: 272px;
    font-family: "Marcellus", serif; font-size: 31px; letter-spacing: 1px;
  }
  .divider { position: absolute; left: 52px; top: 316px; width: 693px; height: 1px; background: var(--rule); }

  .contact { position: absolute; left: 52px; top: 326px; font-size: 20px; line-height: 26px; list-style: none; }
  .contact li { display: flex; align-items: center; gap: 10px; }
  .contact svg { width: 16px; height: 16px; fill: var(--ink); }

  .company { position: absolute; right: 55px; top: 326px; text-align: right; font-size: 20px; line-height: 26px; }

  .band { position: absolute; left: 0; top: 406px; width: 800px; height: 52px; }
  .website {
    position: absolute; right: 55px; top: 418px; font-size: 19px; color: var(--band-text);
  }

  .services-title {
    position: absolute; left: 55px; top: 44px;
    font-family: "Marcellus", serif; font-size: 26px;
  }
  .services-list { position: absolute; left: 55px; top: 86px; list-style: none; font-size: 20px; line-height: 29.4px; }
  .services-list li { display: flex; align-items: center; }
  .services-list li::before {
    content: ""; width: 9px; height: 9px; background: var(--ink); margin-right: 15px; flex: none;
  }

  .decoration {
    position: absolute; left: 370px; top: 136px; width: 430px; height: 322px;
    background: linear-gradient(160deg, var(--card) 0%, var(--card-soft) 100%);
  }
</style>
</head>
<body>

  <section class="card card--front">
    <div class="brand-name">HARBORLINE BUILDERS</div>

    <h1 class="person-name">MARCUS DELLING</h1>
    <div class="divider"></div>

    <ul class="contact">
      <li>
        <svg viewBox="0 0 24 24" aria-hidden="true"><path d="M6.6 10.8a15.2 15.2 0 0 0 6.6 6.6l2.2-2.2c.3-.3.7-.4 1-.2 1.1.4 2.3.6 3.6.6.6 0 1 .4 1 1V20c0 .6-.4 1-1 1A17 17 0 0 1 3 4c0-.6.4-1 1-1h3.5c.6 0 1 .4 1 1 0 1.3.2 2.5.6 3.6.1.3 0 .7-.2 1z"/></svg>
        858-471-6093
      </li>
      <li>
        <svg viewBox="0 0 24 24" aria-hidden="true"><path d="M2 6h20v13H2z M2 6l10 7 10-7" fill="none" stroke="#fff" stroke-width="2"/></svg>
        info@brightoakbuilders.com
      </li>
    </ul>

    <div class="company">
      Harborline Builders Inc.<br>
      Licensed General Contractors
    </div>

    <svg class="band" viewBox="0 0 800 52" aria-hidden="true">
      <polygon points="0,12 450,12 430,30 0,30" fill="var(--band-light)"/>
      <polygon points="450,0 800,0 800,52 0,52 0,30 430,30" fill="var(--band-grey)"/>
    </svg>
    <div class="website">www.brightoakbuilders.com</div>
  </section>

  <section class="card card--back">
    <h2 class="services-title">SERVICES</h2>
    <ul class="services-list">
      <li>Remodel : Kitchen &amp; Bath</li>
      <li>Painting : Interior &amp; Exterior</li>
      <li>Flooring : Carpet, Vinyl, Wood</li>
      <li>Window &amp; Door Replacement</li>
      <li>Plumbing : Repairs &amp; Upgrades</li>
      <li>Energy- Efficient Upgrades</li>
      <li>Deck &amp; Pation Construction</li>
      <li>Water &amp; Mold Damage</li>
      <li>Garage Renovation</li>
    </ul>
    <div class="decoration" role="img" aria-label="Large line-art brand decoration area"></div>
  </section>

</body>
</html>
```